Relaydeck Tech Company Website B2B Dev Teams Orbitix

We need a completely new website for this tech company. We offer software as a service to companies that have private Orbitix software. Our clients are developers, tech teams, and companies (B2B). We offer a way to keep Orbitix devices updated worldwide without needing a Vantora Shelf account, which suits corporate-owned single-use devices very well.
Our public is technicians (software developers), not people who use smartphones. Most clients run Relaydeck on tablets, drones, point-of-sale devices, etc.
The most used feature is the background update, which requires no user interaction. Our product helps developers keep their private enterprise applications updated. Some references of what developers like to see:
mivorin.example, taskobri.example, flowquenta.example, dravelo.example, kondrix.example
The green doesn't suit it very well. Feel free to change the logo's color (source images .ai .psd attached). The current website has only five small pages. The new one can have five at most (it can have less). The images of the "update strategies" aren't good. It can be replaced by "mock-like" images mimicking how Orbitix interacts with the user. The proportion of the tool icons isn't good. The login and signup forms can be improved a lot.
We hope for a modern website for a tech company with new colors that, at first glance, convey a sense of quality. We want the current standard for SaaS (software as a service) providers' websites.
https://www.relaydeck-app.example/
NO WORDPRESS.
We want it built using Next, Nuxt, or another good static build tool.

Target Market(s)
Orbitix Software Development
Industry/Entity Type
Software
Coding
Coded - Design and coding required
Number of Pages Required
4 page
Requirements
Must have
- We want it built using Next, Nuxt, or another good static build tool

Nice to have
- Orbitix message notification mockups instead screenshots

Should not have
- wordpress

```html
<!DOCTYPE html>
<html lang="en">
<head>
<meta charset="utf-8">
<title>Relaydeck — Login</title>
<link rel="stylesheet" href="https://fonts.googleapis.com/css2?family=Poppins:wght@400;500;600;700&display=swap">
<style>
  :root {
    --page-bg: #f2f2f2;
    --navy: #0b0b63;
    --brand-blue: #0a3f86;
    --brand-blue-light: #0e5aa8;
    --band: #e1eaf1;
    --field: #f2f2f2;
    --ink: #111111;
    --muted: #555555;
    --line: #d4d4d4;
    --white: #ffffff;
  }
  * { box-sizing: border-box; margin: 0; padding: 0; }
  html, body { width: 1200px; height: 1132px; overflow: hidden; }
  body {
    position: relative;
    background: var(--page-bg);
    font-family: "Poppins", sans-serif;
    color: var(--ink);
  }
  .abs { position: absolute; }

  .brand { font-family: "Poppins", sans-serif; font-weight: 700; color: var(--navy); letter-spacing: -0.5px; }
  .site-header .brand { left: 37px; top: 28px; font-size: 31px; line-height: 40px; }

  .main-nav {
    left: 408px; top: 30px; width: 391px; height: 38px;
    background: #ececec; border-radius: 19px;
    display: flex; align-items: center; justify-content: space-evenly;
    font-size: 13px; text-transform: uppercase; color: var(--ink);
  }
  .btn {
    display: flex; align-items: center; justify-content: center; gap: 6px;
    border-radius: 21px; font-weight: 600; font-size: 11.5px; text-transform: uppercase;
  }
  .btn-outline { border: 1.5px solid var(--navy); color: var(--navy); background: transparent; }
  .btn-solid { background: var(--navy); color: var(--white); }
  .btn-gradient { background: linear-gradient(90deg, var(--brand-blue-light), var(--navy)); color: var(--white); }

  .breadcrumb-band { left: 0; top: 88px; width: 1200px; height: 42px; background: var(--band); }
  .breadcrumb { left: 37px; top: 101px; font-size: 12px; display: flex; gap: 9px; }
  .breadcrumb .current { color: var(--brand-blue); font-weight: 600; }

  .page-title { left: 0; width: 1200px; top: 195px; text-align: center; font-size: 30px; font-weight: 600; }

  .login-card {
    left: 282px; top: 279px; width: 671px; height: 334px;
    background: var(--white); border: 1px solid #e2e2e2; border-radius: 20px;
  }
  .field {
    left: 318px; width: 600px; height: 39px; background: var(--field); border-radius: 6px;
    font-size: 12px; padding-left: 22px; display: flex; align-items: center;
  }
  .form-links { left: 318px; top: 424px; width: 600px; display: flex; justify-content: space-between; font-size: 9.5px; }
  .form-links a { color: var(--brand-blue); font-weight: 600; text-decoration: underline; }

  .human-check {
    left: 508px; top: 460px; width: 220px; height: 52px;
    background: #f9f9f9; border: 1px solid #d3d3d3; border-radius: 3px;
  }
  .human-check .box { position: absolute; left: 10px; top: 14px; width: 24px; height: 24px; background: #fff; border: 2px solid #c1c1c1; border-radius: 2px; }
  .human-check .label { position: absolute; left: 42px; top: 17px; font-size: 12px; color: #222; font-family: "Poppins", sans-serif; }
  .human-check .mark { position: absolute; left: 181px; top: 8px; width: 18px; height: 18px; border-radius: 50%; background: #8fa8d6; }
  .human-check .fine { position: absolute; right: 6px; top: 30px; width: 60px; text-align: center; font-size: 6px; color: #777; line-height: 9px; }

  .sign-in { left: 553px; top: 537px; width: 129px; height: 41px; border: 1px solid var(--ink); border-radius: 21px; font-weight: 600; font-size: 11px; color: var(--ink); }

  .footer-rule { left: 0; top: 708px; width: 1200px; height: 1px; background: var(--line); }
  .site-footer .brand { left: 140px; top: 805px; font-size: 36px; line-height: 48px; }
  .tagline { left: 140px; top: 882px; width: 300px; font-size: 13px; line-height: 21px; color: #222; }

  .footer-col h3 { font-size: 18px; font-weight: 500; color: var(--navy); margin-bottom: 13px; }
  .footer-col ul { list-style: none; }
  .footer-col li { font-size: 16.5px; color: #333; height: 37px; display: flex; align-items: flex-start; gap: 10px; }
  .footer-col li svg { margin-top: 6px; flex: none; }

  .to-top { left: 1141px; top: 1003px; width: 28px; height: 28px; background: #e3e3e3; border-radius: 5px; display: flex; align-items: center; justify-content: center; }

  .bottom-bar { left: 0; top: 1081px; width: 1200px; height: 51px; background: var(--navy); }
  .social { top: 1093px; width: 28px; height: 28px; border-radius: 50%; border: 1px solid rgba(255,255,255,0.7); }
  .social.active { background: var(--white); }
</style>
</head>
<body>
  <header class="site-header">
    <div class="abs brand">Relaydeck</div>
    <nav class="abs main-nav"><span>Home</span><span>Features</span><span>Pricing</span><span>Docs</span><span>Status</span></nav>
    <a class="abs btn btn-outline" style="left:959px;top:28px;width:97px;height:41px;">
      <svg width="16" height="16" viewBox="0 0 16 16" fill="none" stroke="currentColor" stroke-width="1.3"><path d="M7 2h6v12H7M1 8h8M6 5l3 3-3 3"/></svg>Login</a>
    <a class="abs btn btn-gradient" style="left:1068px;top:28px;width:98px;height:41px;">Sign Up</a>
  </header>

  <div class="abs breadcrumb-band"></div>
  <div class="abs breadcrumb"><span>Home</span><span>»</span><span class="current">Login</span></div>

  <h1 class="abs page-title">Login</h1>

  <main>
    <div class="abs login-card"></div>
    <div class="abs field" style="top:314px;">Enter Your Email Address*</div>
    <div class="abs field" style="top:374px;">Password*</div>
    <div class="abs form-links"><span>New Customer? <a>Create Account</a></span><a>Forgot Your Password?</a></div>
    <div class="abs human-check">
      <span class="box"></span><span class="label">I'm not a robot</span>
      <span class="mark"></span><span class="fine">HumanCheck<br>Privacy - Terms</span>
    </div>
    <div class="abs btn sign-in">Sign In</div>
  </main>

  <div class="abs footer-rule"></div>

  <footer class="site-footer">
    <div class="abs brand">Relaydeck</div>
    <p class="abs tagline">Keep your private orbitix application self-updated without any third-party process.</p>
    <a class="abs btn btn-outline" style="left:140px;top:963px;width:98px;height:41px;">
      <svg width="16" height="16" viewBox="0 0 16 16" fill="none" stroke="currentColor" stroke-width="1.3"><path d="M7 2h6v12H7M1 8h8M6 5l3 3-3 3"/></svg>Login</a>
    <a class="abs btn btn-solid" style="left:250px;top:963px;width:97px;height:41px;">Sign Up</a>

    <div class="abs footer-col" style="left:487px;top:800px;">
      <h3>Quick Links</h3>
      <ul>
        <li><svg width="8" height="10" viewBox="0 0 8 10"><path d="M2 1l4 4-4 4" fill="none" stroke="#333" stroke-width="1.4"/></svg>Home</li>
        <li><svg width="8" height="10" viewBox="0 0 8 10"><path d="M2 1l4 4-4 4" fill="none" stroke="#333" stroke-width="1.4"/></svg>Features</li>
        <li><svg width="8" height="10" viewBox="0 0 8 10"><path d="M2 1l4 4-4 4" fill="none" stroke="#333" stroke-width="1.4"/></svg>Pricing</li>
        <li><svg width="8" height="10" viewBox="0 0 8 10"><path d="M2 1l4 4-4 4" fill="none" stroke="#333" stroke-width="1.4"/></svg>Docs</li>
        <li><svg width="8" height="10" viewBox="0 0 8 10"><path d="M2 1l4 4-4 4" fill="none" stroke="#333" stroke-width="1.4"/></svg>Status</li>
      </ul>
    </div>
    <div class="abs footer-col" style="left:663px;top:800px;">
      <h3>Our Features</h3>
      <ul>
        <li><svg width="8" height="10" viewBox="0 0 8 10"><path d="M2 1l4 4-4 4" fill="none" stroke="#333" stroke-width="1.4"/></svg>Host your apk</li>
        <li><svg width="8" height="10" viewBox="0 0 8 10"><path d="M2 1l4 4-4 4" fill="none" stroke="#333" stroke-width="1.4"/></svg>Devices Enrollment</li>
        <li><svg width="8" height="10" viewBox="0 0 8 10"><path d="M2 1l4 4-4 4" fill="none" stroke="#333" stroke-width="1.4"/></svg>Manage Versions</li>
        <li><svg width="8" height="10" viewBox="0 0 8 10"><path d="M2 1l4 4-4 4" fill="none" stroke="#333" stroke-width="1.4"/></svg>Track Installations</li>
        <li><svg width="8" height="10" viewBox="0 0 8 10"><path d="M2 1l4 4-4 4" fill="none" stroke="#333" stroke-width="1.4"/></svg>View All</li>
      </ul>
    </div>
    <div class="abs footer-col" style="left:880px;top:800px;">
      <h3>Other Links</h3>
      <ul>
        <li><svg width="8" height="10" viewBox="0 0 8 10"><path d="M2 1l4 4-4 4" fill="none" stroke="#333" stroke-width="1.4"/></svg>Terms &amp; Conditions</li>
        <li><svg width="8" height="10" viewBox="0 0 8 10"><path d="M2 1l4 4-4 4" fill="none" stroke="#333" stroke-width="1.4"/></svg>Privacy Policy</li>
        <li><svg width="8" height="10" viewBox="0 0 8 10"><path d="M2 1l4 4-4 4" fill="none" stroke="#333" stroke-width="1.4"/></svg>Sitemap</li>
        <li><svg width="8" height="10" viewBox="0 0 8 10"><path d="M2 1l4 4-4 4" fill="none" stroke="#333" stroke-width="1.4"/></svg>Contact Us</li>
      </ul>
    </div>

    <div class="abs to-top"><svg width="10" height="12" viewBox="0 0 10 12"><path d="M5 11V1M1 5l4-4 4 4" fill="none" stroke="#333" stroke-width="1.2"/></svg></div>

    <div class="abs bottom-bar"></div>
    <span class="abs social" style="left:916px;"></span>
    <span class="abs social active" style="left:953px;"></span>
    <span class="abs social" style="left:991px;"></span>
    <span class="abs social" style="left:1029px;"></span>
  </footer>
</body>
</html>
```